Charity Initiative needs a WebPage design

We need a web design for charity initiative by two young guys riding their bikes around Australia to support HarbourLight which helps people with depression and anxiety. Full brief and requirements are attached in the PDF and word document. We have the logo already done and attached. Website will be done in Wordpress and need to get Donations, display current donations, show live Video feed, GPS tracker, Blogs etc and also ability to sell merchandise later

Target Market(s)

Sponsors, Business, Young People

Number of Pages Required

4 page

Font styles to use
Serif
Sans Serif
Decorative
Script

Requirements
Must have
• As per Brief and also Donation status etc
Nice to have
• Please check my logo and read the Bried

```html
<!DOCTYPE html>
<html lang="en">
<head>
<meta charset="utf-8">
<title>Ride the Outback – The Motorcycle Adventure Around Australia</title>
<link href="https://fonts.googleapis.com/css2?family=Open+Sans:wght@400;600;700;800&family=Oswald:wght@500;700&display=swap" rel="stylesheet">
<style>
:root{
  --pink:#e2206f;
  --teal:#3db4b0;
  --ink:#2b2b2b;
  --muted:#8a8a8a;
  --line:#e3e3e3;
  --stat:#a59d95;
  --footer:#262626;
  --white:#ffffff;
}
*{box-sizing:border-box;margin:0;padding:0}
html,body{width:1200px;height:3000px;overflow:hidden}
body{font-family:"Open Sans",Arial,sans-serif;color:var(--ink);position:relative}
.backdrop{position:absolute;inset:0;background:linear-gradient(180deg,#8fc3dc 0%,#c7dbe4 20%,#c98366 38%,#a85a3f 55%,#b9a38a 75%,#8d8d8f 100%)}
.page{position:absolute;left:140px;top:28px;width:920px;height:2950px;background:var(--white);border-top:6px solid var(--pink)}
.abs{position:absolute}
/* header */
.brand{left:10px;top:14px;display:flex;align-items:center;gap:10px;font-family:"Oswald",sans-serif;font-weight:700;font-size:26px;color:var(--pink);text-transform:uppercase}
.brand .dot{width:36px;height:36px;border-radius:50%;background:var(--teal)}
.follow{right:14px;top:14px;display:flex;align-items:center;gap:6px;font-size:11px;font-weight:700;color:var(--muted)}
.follow i{width:18px;height:18px;border-radius:50%;background:var(--teal);display:inline-block}
.follow i:nth-child(3){background:var(--pink)}
.nav{right:14px;top:58px;display:flex;gap:26px;font-size:12px;font-weight:700;align-items:center}
.nav a{color:var(--ink);text-decoration:none;padding-bottom:10px}
.nav a.on{color:var(--pink);border-bottom:3px solid var(--pink)}
/* hero */
.hero{left:10px;top:108px;width:900px;height:400px;background:linear-gradient(180deg,#d9d6cf 0%,#b7ad9c 45%,#8b6a43 75%,#5d4830 100%)}
.hero-title{left:40px;top:140px;font-family:"Oswald",sans-serif;font-weight:700;font-size:62px;line-height:1;color:var(--white);text-transform:uppercase}
/* intro */
.intro h1{font-size:24px;font-weight:800;line-height:1.25}
.intro p{font-size:11px;color:var(--muted);line-height:1.6;margin-top:12px;width:400px}
.stats{display:flex;gap:22px;margin-top:18px}
.stat span{display:block;font-size:10px;font-weight:700;color:var(--muted);text-align:center;margin-bottom:4px}
.stat b{display:block;background:var(--stat);color:var(--white);font-size:24px;font-weight:700;padding:4px 14px;text-align:center}
.btn{display:inline-block;background:var(--pink);color:var(--white);font-size:10px;font-weight:700;padding:7px 12px;text-transform:uppercase}
.video{left:490px;top:535px;width:420px;height:290px;background:linear-gradient(160deg,#c9c6bd,#8a7d64 60%,#4b3f30)}
.player{left:490px;top:800px;width:420px;height:25px;background:rgba(0,0,0,.55)}
/* posts */
.post{left:10px;width:440px}
.post h2{font-size:17px;font-weight:800;line-height:1.3}
.post .thumb{position:absolute;top:58px;left:0;width:150px;height:140px}
.post .body{position:absolute;top:58px;left:166px;width:274px}
.meta{font-size:10px;color:var(--teal);margin-bottom:8px}
.post p,.card p{font-size:10px;color:var(--muted);line-height:1.6;margin-bottom:10px}
/* sidebar */
.side{left:630px;width:280px}
.side h3{font-size:13px;font-weight:800;border-bottom:2px solid var(--line);padding-bottom:8px;margin-bottom:12px}
.field{height:26px;border:1px solid var(--line);font-size:10px;color:var(--muted);padding:6px 8px;margin-bottom:8px}
.bar{height:12px;background:var(--line);margin-top:6px}
.bar div{width:38%;height:100%;background:var(--pink)}
/* journal */
.section-title{font-size:17px;font-weight:800;text-align:center;width:100%}
.card{width:285px}
.card .thumb{position:absolute;left:0;top:0;width:120px;height:170px}
.card .txt{position:absolute;left:132px;top:0;width:150px}
.card h4{font-size:10px;font-weight:800;margin-bottom:6px}
.more{font-size:9px;font-weight:700;color:var(--pink)}
/* cause band */
.cause{left:0;top:2340px;width:920px;height:220px;background:var(--teal)}
.cause-logo{left:24px;top:2360px;width:180px;height:180px;border-radius:50%;background:var(--white);display:flex;align-items:center;justify-content:center;font-weight:700;color:var(--teal);font-size:16px}
.cause h3{font-size:20px;font-weight:800;color:var(--white)}
.cause-text p{font-size:10px;color:#e8f7f6;line-height:1.6;margin-top:8px;width:640px}
/* riders */
.riders h3{font-size:20px;font-weight:800}
.riders p{font-size:10px;color:var(--muted);line-height:1.6;margin-top:12px;width:400px}
.rider{top:2590px;width:220px;height:270px}
/* footer */
.footer{left:0;top:2890px;width:920px;height:60px;background:var(--footer);color:#bbb;font-size:10px;display:flex;align-items:center;justify-content:space-between;padding:0 16px}
.footer .follow{position:static}
</style>
</head>
<body>
<div class="backdrop" role="img" aria-label="Background photo of red outback rock ranges under a blue sky with a road"></div>

<div class="page">
  <header>
    <div class="abs brand"><span class="dot"></span>Ride the Outback</div>
    <div class="abs follow">FOLLOW US ON <i></i><i></i><i></i><i></i></div>
    <nav class="abs nav">
      <a class="on">HOME</a><a>JOURNAL</a><a>RIDERS</a><a>SUPPORTERS</a><a>CONTACT</a>
      <svg width="14" height="14" viewBox="0 0 14 14"><circle cx="6" cy="6" r="4.5" fill="none" stroke="#2b2b2b" stroke-width="1.8"/><line x1="9.5" y1="9.5" x2="13" y2="13" stroke="#2b2b2b" stroke-width="1.8"/></svg>
    </nav>
  </header>

  <div class="abs hero" role="img" aria-label="Rider on an adventure motorcycle on a dusty outback track"></div>
  <div class="abs hero-title">Ride<br>the Outback</div>

  <section class="abs intro" style="left:10px;top:535px">
    <h1>The Motorcycle Adventure Around<br>Australia!</h1>
    <p>Two mates, two bikes and one big loop of the country, riding to raise funds and start honest talks about depression and anxiety.</p>
    <div class="stats">
      <div class="stat"><span>DAYS</span><b>152</b></div>
      <div class="stat"><span>KILOMETERS</span><b>54,458</b></div>
      <div class="stat"><span>PROVINCES</span><b>44</b></div>
    </div>
    <a class="btn" style="margin-top:20px">Donate Now !</a>
  </section>
  <div class="abs video" role="img" aria-label="Live video feed of the riders on dirt bikes"></div>
  <div class="abs player"><svg width="30" height="25" viewBox="0 0 30 25"><polygon points="11,7 20,12.5 11,18" fill="#fff"/></svg></div>

  <!-- posts -->
  <article class="abs post" style="top:900px">
    <h2>Temporibus autem quibusdam et aut officiis debitis au trerum necessitatibus</h2>
    <div class="thumb" role="img" aria-label="Riders on a gravel road" style="background:linear-gradient(160deg,#c7c9c4,#7d7868)"></div>
    <div class="body"><div class="meta">22/07/2016 &nbsp;|&nbsp; 5 Comments</div><p>Day one out of the city and the road is already testing us. Long dusty stretches, warm locals and a sunset worth every sore muscle along the way.</p><a class="btn">Read More »</a></div>
  </article>
  <article class="abs post" style="top:1165px">
    <h2>Temporibus autem quibusdam et aut officiis debitis au trerum necessitatibus</h2>
    <div class="thumb" role="img" aria-label="Two motorcycles parked by red cliffs" style="background:linear-gradient(160deg,#b7b2a7,#8a4b3a)"></div>
    <div class="body"><div class="meta">22/07/2016 &nbsp;|&nbsp; 5 Comments</div><p>We camped beside the cliffs tonight and talked with a family who shared their own story. Those chats are the reason this ride exists at all.</p><a class="btn">Read More »</a></div>
  </article>
  <article class="abs post" style="top:1430px">
    <h2>Temporibus autem quibusdam et aut officiis debitis au trerum necessitatibus</h2>
    <div class="thumb" role="img" aria-label="Loaded motorcycle on a desert track" style="background:linear-gradient(160deg,#c8b79c,#6b5a44)"></div>
    <div class="body"><div class="meta">22/07/2016 &nbsp;|&nbsp; 5 Comments</div><p>A flat tyre, a broken strap and forty degrees of heat. We fixed it all by lunch, laughed about it later and kept rolling north.</p><a class="btn">Read More »</a></div>
  </article>
  <article class="abs post" style="top:1695px">
    <h2>Temporibus autem quibusdam et aut officiis debitis au trerum necessitatibus</h2>
    <div class="thumb" role="img" aria-label="Open coastal road under blue sky" style="background:linear-gradient(180deg,#6fb0dc,#c9c3b2)"></div>
    <div class="body"><div class="meta">22/07/2016 &nbsp;|&nbsp; 5 Comments</div><p>The coast road delivered blue skies and empty bends. Thanks to everyone who donated this week, you pushed us past a big milestone.</p><a class="btn">Read More »</a></div>
  </article>

  <!-- sidebar -->
  <aside class="abs side" style="top:900px">
    <h3>Join Us For The Ride</h3>
    <div class="field">Name</div>
    <div class="field">Email</div>
    <a class="btn">Join Us</a>
  </aside>
  <aside class="abs side" style="top:1060px">
    <h3>Total Funds Raised</h3>
    <div style="font-size:10px;color:var(--muted);display:flex;justify-content:space-between"><span>Raised So Far</span><b style="color:var(--ink)">$52,356</b></div>
    <div class="bar"><div></div></div>
  </aside>
  <aside class="abs side" style="top:1170px">
    <h3>GPS Tracker</h3>
    <div role="img" aria-label="Map of Australia with the riders' route marked" style="height:200px;background:linear-gradient(160deg,#e9ede6,#cfd9cf)"></div>
  </aside>
  <aside class="abs side" style="top:1420px">
    <h3>Join Us on Friendbook</h3>
    <div style="border:1px solid var(--line);height:200px;position:relative">
      <div role="img" aria-label="Page cover photo" style="height:90px;background:linear-gradient(160deg,#b6c6d3,#7b8a97)"></div>
      <div style="padding:8px;font-size:10px;font-weight:700">Ride the Outback</div>
      <div style="display:flex;gap:4px;padding:0 8px">
        <span style="width:40px;height:40px;background:#ccc"></span><span style="width:40px;height:40px;background:#bbb"></span><span style="width:40px;height:40px;background:#ccc"></span><span style="width:40px;height:40px;background:#bbb"></span><span style="width:40px;height:40px;background:#ccc"></span>
      </div>
    </div>
  </aside>

  <!-- journal -->
  <h2 class="abs section-title" style="top:2000px">Most Recent Journal Entries</h2>
  <div class="abs card" style="left:10px;top:2050px">
    <div class="thumb" role="img" aria-label="Rider beside a motorcycle" style="background:linear-gradient(160deg,#d2cfc8,#7a7366)"></div>
    <div class="txt"><h4>Similique sunt in culpa qui officia deserunt mollitia animi</h4><p>Notes from a long week on the road, the people we met and the kindness we found in small towns.</p><span class="more">READ MORE »</span></div>
  </div>
  <div class="abs card" style="left:318px;top:2050px">
    <div class="thumb" role="img" aria-label="Magazine cover featuring the ride" style="background:linear-gradient(180deg,#9cc3de,#6d6a63)"></div>
    <div class="txt"><h4>Similique sunt in culpa qui officia deserunt mollitia animi</h4><p>We made the cover of a riding magazine this month, a huge boost for getting the message out.</p><span class="more">READ MORE »</span></div>
  </div>
  <div class="abs card" style="left:626px;top:2050px">
    <div class="thumb" role="img" aria-label="Motorcycle on a gravel road" style="background:linear-gradient(160deg,#c4bba9,#6b6353)"></div>
    <div class="txt"><h4>Similique sunt in culpa qui officia deserunt mollitia animi</h4><p>Halfway there. A look back at the distance covered and the support that keeps us going each day.</p><span class="more">READ MORE »</span></div>
  </div>

  <!-- cause -->
  <div class="abs cause"></div>
  <div class="abs cause-logo">HarbourLight</div>
  <div class="abs cause-text" style="left:230px;top:2375px">
    <h3>HarbourLight</h3>
    <p>HarbourLight works to reduce the impact of depression and anxiety in the community by raising awareness, fighting stigma and helping people find the right support. Every dollar raised on this ride goes straight to their programs, helplines and local outreach across Australia.</p>
    <a class="btn" style="margin-top:12px">Donate Now !</a>
  </div>

  <!-- riders -->
  <section class="abs riders" style="left:10px;top:2590px">
    <h3>Meet Our Riders</h3>
    <p>We are two young mates who love bikes and believe nobody should face depression or anxiety alone. After watching friends struggle, we decided to ride the whole country to raise money and get people talking openly about mental health.</p>
    <span class="more" style="display:block;margin-top:14px">READ MORE »</span>
  </section>
  <div class="abs rider" style="left:460px" role="img" aria-label="Portrait photo of the first rider"></div>
  <div class="abs rider" style="left:460px;background:linear-gradient(160deg,#d8c6ae,#8c7258)"></div>
  <div class="abs rider" style="left:690px;background:linear-gradient(160deg,#c8bba7,#7d6a57)" role="img" aria-label="Portrait photo of the second rider"></div>

  <footer class="abs footer">
    <span>© 2016 Ride the Outback. All rights reserved.</span>
    <span class="follow">FOLLOW US ON <i></i><i></i><i></i><i></i></span>
  </footer>
</div>
</body>
</html>
```